Blue Harbor Inc - Cutting-Edge Biotech Laboratory - Sleek & Sophisticated

Please design a website that has more of a high-tech and high-end feel, with contents outlined in the uploaded file.

Please have main tabs of the following categories: Home, About, FDA & LAWS, Science, Products, Media, Contact.

Media can include all the videos and photos.

Current website: www.blueharborlabs.com - it needs to be much more high-end, sleek and more organized. Please do NOT follow the outlines in the old website, but follow the uploaded CONTENT file.

Target Market(s)

doctors

Industry/Entity Type

Biotechnology

Coding

Coded - Design and coding required

Number of Pages Required

5+ page

Requirements
Must have
• Logo
Nice to have
• Some lotion on the website

```html
<!DOCTYPE html>
<html lang="en">
<head>
<meta charset="utf-8">
<title>Blue Harbor Inc</title>
<link href="https://fonts.googleapis.com/css2?family=Lato:ital,wght@0,400;0,700;0,900;1,400&family=Open+Sans:wght@400;600;700&display=swap" rel="stylesheet">
<style>
:root{
  --ink:#1c1c1c;
  --muted:#6f6f6f;
  --gold:#a38b5f;
  --gold-soft:#c9b48a;
  --dark:#1a1a1a;
  --footer:#1d1d1d;
  --footer-bar:#141414;
  --white:#ffffff;
  --line:#dcdcdc;
  --team-bg:#ececec;
}
*{margin:0;padding:0;box-sizing:border-box}
html,body{width:1200px;height:2542px;overflow:hidden}
body{position:relative;background:var(--white);font-family:"Open Sans",sans-serif;color:var(--ink)}
.abs{position:absolute}

/* header */
.site-header{position:absolute;left:0;top:0;width:1200px;height:105px;background:var(--white)}
.brand{left:100px;top:30px;font-family:"Lato",sans-serif;font-weight:900;font-size:31px;color:#3a3a3a;letter-spacing:.5px}
.top-contact{right:100px;top:26px;display:flex;gap:40px;font-size:14px;color:var(--ink)}
.top-contact span{display:flex;align-items:center;gap:12px}
.main-nav{right:100px;top:60px;display:flex;gap:26px;align-items:center;font-family:"Lato",sans-serif;font-size:17px}
.main-nav a{color:var(--ink);text-decoration:none}
.main-nav a.active{color:var(--gold)}

/* hero */
.hero{left:0;top:105px;width:1200px;height:580px;overflow:hidden}
.hero-bg{position:absolute;inset:0;background:radial-gradient(ellipse at 55% 45%,#5a3a1e 0%,#4a1f14 35%,#2e0f0b 75%,#1c0907 100%)}
.hero-title{left:0;top:110px;width:1200px;text-align:center;font-family:"Open Sans",sans-serif;font-weight:700;font-size:96px;color:var(--white);line-height:1}
.hero-sub{left:0;top:222px;width:1200px;text-align:center;font-family:"Open Sans",sans-serif;font-weight:600;font-size:38px;line-height:50px;color:var(--white)}
.hero-btn{left:522px;top:360px;width:157px;height:45px;border:2px solid var(--white);border-radius:23px;color:var(--white);font-family:"Lato",sans-serif;font-weight:700;font-size:18px;display:flex;align-items:center;justify-content:center}
.hero-dots{left:570px;top:503px;display:flex;gap:7px}
.hero-dots i{width:10px;height:10px;border:1.5px solid var(--white);border-radius:50%;display:block}
.hero-dots i.on{background:var(--white)}
.hero-curve{left:0;top:0}

/* about */
.section-title{font-family:"Lato",sans-serif;font-weight:400;color:var(--ink)}
.about-title{left:100px;top:746px;font-size:32px}
.about-text{left:100px;top:800px;width:479px;font-size:14px;line-height:30px;color:var(--muted);text-align:justify}
.outline-btn{left:101px;top:971px;width:106px;height:38px;border:2px solid var(--ink);border-radius:19px;font-family:"Lato",sans-serif;font-weight:700;font-size:15px;display:flex;align-items:center;justify-content:center}
.video{left:627px;top:754px;width:475px;height:258px;border:3px solid #e6e6e6;background:linear-gradient(135deg,#7a5a36 0%,#c8a06a 40%,#8c6a48 70%,#4a3020 100%)}
.video .play{position:absolute;left:217px;top:109px}
.video-caption{left:627px;top:1016px;font-size:13px;color:var(--ink)}

/* applications */
.applications{left:0;top:1087px;width:1200px;height:362px;background:radial-gradient(ellipse at 50% 30%,#2a2a2a 0%,#161616 70%,#111 100%)}
.app-title{left:0;top:72px;width:1200px;text-align:center;font-family:"Lato",sans-serif;font-size:31px;color:var(--white)}
.app-item{top:130px;width:200px;text-align:center}
.app-item svg{display:block;margin:0 auto}
.app-item p{margin-top:14px;font-family:"Lato",sans-serif;font-size:22px;color:var(--white)}
.pointer{left:574px;top:1448px}

.intro{left:200px;top:1518px;width:800px;text-align:center;font-size:14.5px;line-height:30.5px;color:var(--muted)}
.view-link{left:0;top:1622px;width:1200px;text-align:center;font-size:14px;color:var(--ink)}
.view-link span{border-bottom:1px solid var(--ink)}

/* team */
.team{left:0;top:1717px;width:1200px;height:459px;background:linear-gradient(120deg,#f2f2f2 0%,#e4e4e4 35%,#f4f4f4 60%,#e2e2e2 100%)}
.team-title{left:0;top:68px;width:1200px;text-align:center;font-size:29px}
.member{top:140px;width:260px;text-align:center}
.portrait{width:150px;height:150px;margin:0 auto;border-radius:50%;border:4px solid var(--white);box-shadow:0 0 0 1px #9a9a9a}
.member .name{margin-top:26px;font-family:"Lato",sans-serif;font-style:italic;font-size:13px;color:#333;letter-spacing:.3px}
.member .role{margin-top:6px;font-family:"Lato",sans-serif;font-size:17px;line-height:27px;color:var(--ink)}
.arrow{top:210px}

/* footer */
.site-footer{left:0;top:2176px;width:1200px;height:316px;background:var(--footer);color:var(--white)}
.footer-col{top:72px}
.footer-col h4{font-family:"Lato",sans-serif;font-weight:400;font-size:22px;margin-bottom:18px}
.footer-col ul{list-style:none}
.footer-col li{font-size:13px;line-height:24.7px;padding-left:22px;position:relative}
.footer-col li::before{content:"";position:absolute;left:2px;top:10px;width:6px;height:6px;border-radius:50%;background:var(--white)}
.contact-row{display:flex;gap:18px;font-size:13px;line-height:24px;margin-bottom:6px}
.contact-row svg{flex:none;margin-top:6px}
.newsletter p{font-size:13px;line-height:22px;margin-bottom:12px}
.email-field{width:223px;height:34px;background:var(--white);display:flex;align-items:center;justify-content:space-between;padding:0 12px;color:#888;font-size:13px}
.footer-bar{left:0;top:2492px;width:1200px;height:50px;background:var(--footer-bar);color:var(--white)}
.copyright{left:100px;top:16px;font-size:13px}
.social{right:100px;top:18px;display:flex;gap:24px}
.social i{width:14px;height:14px;border-radius:50%;background:var(--white);display:block}
</style>
</head>
<body>

<header class="site-header">
  <div class="abs brand">BLUE HARBOR</div>
  <div class="abs top-contact">
    <span><svg width="14" height="14" viewBox="0 0 24 24"><path fill="#1c1c1c" d="M6.6 10.8a15 15 0 0 0 6.6 6.6l2.2-2.2c.3-.3.7-.4 1-.2 1.1.4 2.3.6 3.6.6.6 0 1 .4 1 1V20c0 .6-.4 1-1 1A17 17 0 0 1 3 4c0-.6.4-1 1-1h3.5c.6 0 1 .4 1 1 0 1.3.2 2.5.6 3.6.1.3 0 .7-.2 1z"/></svg>5550147392</span>
    <span><svg width="16" height="12" viewBox="0 0 16 12"><path fill="#1c1c1c" d="M0 0h16v1.5L8 7 0 1.5zM0 3.3l8 5.4 8-5.4V12H0z"/></svg>info@blueharborlabs.com</span>
  </div>
  <nav class="abs main-nav">
    <a class="active">Home</a><a>About</a><a>FDA &amp; LAWS</a><a>Science</a><a>Products</a><a>Contact</a>
    <svg width="16" height="16" viewBox="0 0 16 16"><circle cx="6.5" cy="6.5" r="4.8" fill="none" stroke="#1c1c1c" stroke-width="2.2"/><path d="M10 10l4.5 4.5" stroke="#1c1c1c" stroke-width="2.6" stroke-linecap="round"/></svg>
  </nav>
</header>

<section class="abs hero">
  <div class="hero-bg" role="img" aria-label="Magnified view of cells in warm red and amber tones"></div>
  <svg class="abs hero-curve" width="1200" height="580" viewBox="0 0 1200 580">
    <path d="M0 455 Q640 700 1200 450 L1200 580 L0 580 Z" fill="#ffffff"/>
    <path d="M0 455 Q640 700 1200 450" fill="none" stroke="#2a1610" stroke-width="3"/>
  </svg>
  <h1 class="abs hero-title">Blue Harbor</h1>
  <p class="abs hero-sub">Leader in Regenerative Medicine<br>Innovator of the Industry</p>
  <div class="abs hero-btn">Contact Now!</div>
  <div class="abs hero-dots"><i class="on"></i><i></i><i></i><i></i></div>
</section>

<section>
  <h2 class="abs section-title about-title">About Us</h2>
  <p class="abs about-text">Blue Harbor Therapy provides Non-Embryonic Stem Cells and unique protocols to doctors in order to help their patients who face major health conditions, as well as those who simply wish to stay young and healthy. Over the past seven years of development, we have successfully conducted research into major diseases related to kidney.</p>
  <div class="abs outline-btn">Read More</div>
  <div class="abs video" role="img" aria-label="Video still of a seated interview in a warmly lit room">
    <svg class="play" width="40" height="40" viewBox="0 0 40 40"><path d="M6 2 L38 20 L6 38 Z" fill="rgba(255,255,255,.8)"/></svg>
  </div>
  <p class="abs video-caption">Interview with company owner Marco Delgado on stem cells</p>
</section>

<section class="abs applications">
  <div class="abs" style="inset:0" role="img" aria-label="Dark background with faint bubble texture"></div>
  <h2 class="abs app-title">Wide variety of clinical applications</h2>

  <div class="abs app-item" style="left:58px">
    <svg width="112" height="124" viewBox="0 0 112 124"><polygon points="56,3 108,32 108,92 56,121 4,92 4,32" fill="none" stroke="var(--gold)" stroke-width="3"/><polygon points="56,11 101,36 101,88 56,113 11,88 11,36" fill="#111"/><rect x="44" y="36" width="24" height="30" rx="6" fill="#fff"/><rect x="40" y="64" width="10" height="26" rx="4" fill="#fff"/><rect x="62" y="64" width="10" height="26" rx="4" fill="#fff"/></svg>
    <p>Orthopedics</p>
  </div>
  <div class="abs app-item" style="left:271px">
    <svg width="112" height="124" viewBox="0 0 112 124"><polygon points="56,3 108,32 108,92 56,121 4,92 4,32" fill="none" stroke="var(--gold)" stroke-width="3"/><polygon points="56,11 101,36 101,88 56,113 11,88 11,36" fill="#111"/><rect x="36" y="44" width="22" height="40" rx="3" fill="#fff"/><rect x="60" y="52" width="20" height="32" rx="3" fill="#fff"/><rect x="62" y="40" width="16" height="10" fill="#fff"/><path d="M70 60v16M62 68h16" stroke="#111" stroke-width="4"/></svg>
    <p>Sports Medicine</p>
  </div>
  <div class="abs app-item" style="left:486px">
    <svg width="112" height="124" viewBox="0 0 112 124"><polygon points="56,3 108,32 108,92 56,121 4,92 4,32" fill="none" stroke="var(--gold)" stroke-width="3"/><polygon points="56,11 101,36 101,88 56,113 11,88 11,36" fill="#111"/><path d="M56 68 C38 54 40 38 50 38 C54 38 56 42 56 44 C56 42 58 38 62 38 C72 38 74 54 56 68Z" fill="#fff"/><path d="M32 74 Q46 72 56 82 Q68 82 82 72" fill="none" stroke="#fff" stroke-width="5" stroke-linecap="round"/></svg>
    <p>Wound Care</p>
  </div>
  <div class="abs app-item" style="left:700px">
    <svg width="112" height="124" viewBox="0 0 112 124"><polygon points="56,3 108,32 108,92 56,121 4,92 4,32" fill="none" stroke="var(--gold)" stroke-width="3"/><polygon points="56,11 101,36 101,88 56,113 11,88 11,36" fill="#111"/><path d="M44 44 Q56 36 68 44 L66 70 Q64 92 54 92 Q44 92 46 72 Z" fill="#fff"/></svg>
    <p>Podiatry</p>
  </div>
  <div class="abs app-item" style="left:914px">
    <svg width="112" height="124" viewBox="0 0 112 124"><polygon points="56,3 108,32 108,92 56,121 4,92 4,32" fill="none" stroke="var(--gold)" stroke-width="3"/><polygon points="56,11 101,36 101,88 56,113 11,88 11,36" fill="#111"/><path d="M40 88 V72 Q30 60 36 48 Q44 34 60 36 Q76 38 78 54 L84 66 L78 68 V78 H66 V88 Z" fill="#fff"/><circle cx="60" cy="56" r="7" fill="none" stroke="#111" stroke-width="4"/></svg>
    <p>Pain Management</p>
  </div>
</section>
<svg class="abs pointer" width="52" height="26" viewBox="0 0 52 26"><path d="M0 0 H52 L26 26 Z" fill="#141414"/></svg>

<p class="abs intro">Blue Harbor Inc has developed innovative processes and safety protocols, which deliver the highest cellular tissue viability and safety standards. With these safety and quality standards, Blue Harbor has become the leader of birth tissue allografts in the field of regenerative medicine.</p>
<p class="abs view-link"><span>View details</span></p>

<section class="abs team">
  <h2 class="abs section-title team-title">Our Team</h2>
  <svg class="abs arrow" style="left:100px" width="14" height="22" viewBox="0 0 14 22"><path d="M12 2 L3 11 L12 20" fill="none" stroke="#8a8a8a" stroke-width="3"/></svg>
  <svg class="abs arrow" style="left:1086px" width="14" height="22" viewBox="0 0 14 22"><path d="M2 2 L11 11 L2 20" fill="none" stroke="#8a8a8a" stroke-width="3"/></svg>
  <div class="abs member" style="left:200px">
    <div class="portrait" role="img" aria-label="Portrait photo of Marco Delgado" style="background:linear-gradient(160deg,#6c8a5a,#3c5a3e 60%,#2a3c5e)"></div>
    <p class="name">MARCO DELGADO</p>
    <p class="role">Stem Cell Technology<br>Chief Scientist</p>
  </div>
  <div class="abs member" style="left:470px">
    <div class="portrait" role="img" aria-label="Portrait photo of Dana Whitlow" style="background:linear-gradient(160deg,#e8e2d6,#d6c39a 55%,#b9a27e)"></div>
    <p class="name">DANA WHITLOW</p>
    <p class="role">Stem Cell Project<br>Manager</p>
  </div>
  <div class="abs member" style="left:740px">
    <div class="portrait" role="img" aria-label="Portrait photo of Dr. Peter L. Ames" style="background:linear-gradient(160deg,#d9d2c8,#a07a62 55%,#2a2a2a)"></div>
    <p class="name">DR. PETER L. AMES</p>
    <p class="role">Ames Center for Cardiac<br>Longevity</p>
  </div>
</section>

<footer class="abs site-footer">
  <div class="abs footer-col" style="left:102px">
    <h4>Quick Links</h4>
    <ul><li>Home</li><li>About</li><li>FDA &amp; LAWS</li><li>Science</li><li>Products</li><li>Contact</li></ul>
  </div>
  <div class="abs footer-col" style="left:312px">
    <h4>Other Links</h4>
    <ul><li>HCT/ps</li><li>Texas Regulations</li><li>Terms Of Use</li><li>Privacy Policy</li></ul>
  </div>
  <div class="abs footer-col" style="left:536px;width:300px">
    <h4>Contact Us</h4>
    <div class="contact-row"><svg width="12" height="12" viewBox="0 0 12 12"><path d="M12 0 L0 5 L5 7 L7 12 Z" fill="#fff"/></svg><span>Blue Harbor Labs, 2100 harbor view<br>Road, lakeside, mi, 48000</span></div>
    <div class="contact-row"><svg width="13" height="10" viewBox="0 0 13 10"><rect x=".75" y=".75" width="11.5" height="8.5" fill="none" stroke="#fff" stroke-width="1.5"/><path d="M1 1 L6.5 5.5 L12 1" fill="none" stroke="#fff" stroke-width="1.5"/></svg><span>info@blueharborlabs.com</span></div>
    <div class="contact-row"><svg width="12" height="12" viewBox="0 0 24 24"><path fill="#fff" d="M6.6 10.8a15 15 0 0 0 6.6 6.6l2.2-2.2c.3-.3.7-.4 1-.2 1.1.4 2.3.6 3.6.6.6 0 1 .4 1 1V20c0 .6-.4 1-1 1A17 17 0 0 1 3 4c0-.6.4-1 1-1h3.5c.6 0 1 .4 1 1 0 1.3.2 2.5.6 3.6.1.3 0 .7-.2 1z"/></svg><span>5550147392</span></div>
  </div>
  <div class="abs footer-col newsletter" style="left:878px">
    <h4>Newsletter</h4>
    <p>Sign up our newsletter to get more<br>information</p>
    <div class="email-field"><span>Email address</span><svg width="14" height="12" viewBox="0 0 14 12"><path d="M0 6 H12 M7 1 L12 6 L7 11" fill="none" stroke="#1c1c1c" stroke-width="2.4"/></svg></div>
  </div>
</footer>

<div class="abs footer-bar">
  <p class="abs copyright">2018 © BlueHarbor. All rights reserved.</p>
  <div class="abs social"><i></i><i></i><i></i><i></i></div>
</div>

</body>
</html>
```